THE WELLNESS BARN WEBSITE for Physio, Fitness, health

An attractive website advertising a physiotherapyand fitness / gym business, not generic, colours are natural, greens, browns, beiges. No cheesy pictures. With the ability to sell a small,amount of goods online if i decide to. Simple to navigate. Text boxes that i can input the main information and change easily. Somewhere to put my timetable. Easy to find contact details. However many pages it needs, im not fussed.
Target Market(s)
People looking for rehabilitation or fitness classes
Industry/Entity Type
Physiotherapy, Fitness, Gym, Health
Coding
Coded - Design and coding required
Number of Pages Required
1 page
Font styles to use
Other font styles liked:
- Im not fusse,ld, not script
Requirements
Must have
- Will upload posts from my business insta page for reference about the feel. Earthy natural tones, I have a lot of timber, and rustic looking piece's, plants etc in my clinic
Nice to have
- Simple to navigate
Should not have
- Cheesy "yoga" or generic "people doing physio" pics

```html
<!DOCTYPE html>
<html lang="en">
<head>
<meta charset="utf-8">
<title>The Wellness Barn – Physio &amp; Fitness</title>
<link rel="stylesheet" href="https://fonts.googleapis.com/css2?family=Poppins:wght@400;500;600;700&display=swap">
<style>
:root{
  --green-dark:#2c4420;
  --green:#3d5c2a;
  --green-mid:#587a3c;
  --green-pale:#eef5e2;
  --beige:#f6f2ea;
  --brown:#6b5238;
  --ink:#1f1f1f;
  --muted:#555;
  --line:#d9d9d9;
  --white:#fff;
  --star:#f4b400;
}
*{box-sizing:border-box;margin:0;padding:0}
html,body{width:1200px;height:3700px;overflow:hidden}
body{font-family:"Poppins",sans-serif;color:var(--ink);background:var(--white);position:relative}
.section{position:absolute;left:0;width:1200px}
.btn{display:inline-block;background:var(--green-dark);color:var(--white);font-weight:600;font-size:16px;border-radius:24px;padding:10px 28px;text-decoration:none}
.btn-light{background:var(--white);color:var(--green-dark)}
h2{font-weight:700;font-size:40px;text-align:center}

/* header */
.site-header{top:0;height:104px;background:var(--white);display:flex;align-items:center;padding:0 60px}
.brand{display:flex;align-items:center;gap:10px;color:var(--green-dark);font-weight:700;font-size:20px}
.brand-dot{width:34px;height:34px;border-radius:50%;background:var(--green-dark)}
.contact-strip{position:absolute;top:8px;left:520px;display:flex;gap:22px;font-size:13px;color:var(--muted);align-items:center}
.contact-strip span{display:flex;align-items:center;gap:6px}
.nav{position:absolute;left:340px;top:52px;display:flex;gap:34px;font-size:16px;font-weight:500}
.nav a{color:var(--ink);text-decoration:none}
.nav a.active{border-bottom:2px solid var(--green-dark);padding-bottom:3px}
.site-header .btn{position:absolute;right:60px;top:44px}

/* hero */
.hero{top:104px;height:496px;background:linear-gradient(120deg,#55603e 0%,#7b8b5d 40%,#a4ad8c 65%,#4d5c34 100%)}
.hero-copy{position:absolute;left:50px;top:120px;width:520px;color:var(--white)}
.hero-copy h1{font-size:50px;line-height:1.15;font-weight:700}
.hero-copy p{font-size:15px;margin:16px 0 24px;line-height:1.5}

/* offer */
.offer{top:600px;height:690px}
.offer h2{margin-top:70px}
.offer h2 span{color:var(--green-mid)}
.offer .intro{width:980px;margin:22px auto 0;text-align:center;font-size:15px;line-height:1.6;color:var(--muted)}
.card-row{position:absolute;left:80px;top:300px;width:1040px;display:flex;gap:44px;justify-content:center}
.offer-card{width:310px;height:300px;position:relative}
.offer-card .photo{width:310px;height:230px;border-radius:14px;background:linear-gradient(140deg,#b39a7a,#6c7d4d)}
.offer-card .label{position:absolute;left:40px;right:40px;top:205px;height:80px;background:var(--white);border:2px solid var(--ink);border-radius:12px;display:flex;align-items:center;justify-content:center;text-align:center;font-weight:600;font-size:17px;line-height:1.3}
.arrow{position:absolute;width:28px;height:28px}

/* team */
.team{top:1300px;height:650px;background:var(--green-pale)}
.team .eyebrow{text-align:center;font-size:14px;font-weight:600;margin-top:80px;color:var(--muted)}
.team h2{margin-top:4px}
.team .sub{text-align:center;font-size:15px;color:var(--muted);margin-top:8px}
.team-row{position:absolute;top:250px;left:110px;display:flex;gap:60px}
.member{width:300px;height:300px;border-radius:14px;position:relative;background:linear-gradient(160deg,#8c7a64,#4d5a3a)}
.member .share{position:absolute;right:12px;top:12px;width:30px;height:30px;border-radius:50%;background:var(--white)}
.member .tag{position:absolute;left:0;bottom:18px;background:rgba(255,255,255,.85);padding:8px 14px;font-size:13px;line-height:1.3}
.member .tag b{display:block;font-weight:600}

/* testimonials */
.stories{top:1960px;height:460px}
.stories h2{margin-top:50px}
.stories h2 span{color:var(--green-mid)}
.stories .sub{text-align:center;font-size:15px;color:var(--muted);margin-top:6px}
.story-row{position:absolute;top:160px;left:110px;display:flex;gap:60px}
.story{width:470px;height:220px;background:var(--white);box-shadow:0 4px 16px rgba(0,0,0,.12);border-radius:6px;padding:24px}
.story .who{display:flex;gap:16px;align-items:center}
.avatar{width:64px;height:64px;border-radius:50%;background:linear-gradient(150deg,#c7ab8d,#7d6a54)}
.story .name{font-weight:600;font-size:17px}
.story .role{font-size:13px;color:var(--muted)}
.stars{color:var(--star);font-size:22px;letter-spacing:2px}
.story p{font-size:14px;color:var(--muted);margin-top:18px;line-height:1.55}

/* contact */
.contact{top:2420px;height:340px;background:linear-gradient(90deg,#253a1b,#3b5428 50%,#253a1b);color:var(--white);text-align:center}
.contact h2{margin-top:40px;font-size:36px;color:var(--white)}
.contact ul{list-style:none;width:300px;margin:20px auto 0;text-align:left;font-size:15px}
.contact li{display:flex;gap:12px;align-items:center;margin-bottom:14px}
.contact .btn{margin-top:10px}

/* faq */
.faq{top:2820px;height:500px}
.faq h2{margin-top:30px}
.faq .sub{width:620px;margin:10px auto 0;text-align:center;font-size:15px;color:var(--muted);line-height:1.5}
.faq-photo{position:absolute;left:220px;top:180px;width:360px;height:280px;background:linear-gradient(130deg,#5b6b44,#a7a282 55%,#3f4c2d)}
.faq-list{position:absolute;left:600px;top:180px;width:490px}
.faq-item{border:1px solid var(--line);border-radius:4px;margin-bottom:12px;background:var(--white)}
.faq-q{display:flex;justify-content:space-between;align-items:center;padding:12px 16px;font-size:15px;font-weight:500}
.faq-a{padding:0 16px 14px;font-size:13px;color:var(--muted);line-height:1.5;border-top:1px solid var(--line);padding-top:12px}
.toggle{width:22px;height:22px;border:1.5px solid var(--ink);border-radius:50%;position:relative}
.toggle::after{content:"";position:absolute;left:5px;right:5px;top:9px;height:1.5px;background:var(--ink)}

/* footer */
.site-footer{top:3360px;height:340px;background:var(--green-dark);color:var(--white)}
.site-footer .brand{position:absolute;left:120px;top:40px;color:var(--white);font-size:22px}
.site-footer .brand-dot{background:var(--white)}
.subscribe{position:absolute;left:120px;top:150px;display:flex}
.subscribe span{width:240px;height:48px;background:var(--white);color:#888;font-size:14px;padding:14px 16px}
.subscribe b{width:52px;height:48px;background:var(--ink);display:flex;align-items:center;justify-content:center}
.socials{position:absolute;left:120px;top:218px;display:flex;gap:10px}
.socials i{width:28px;height:28px;border-radius:50%;background:var(--white);display:block}
.foot-col{position:absolute;top:130px;font-size:14px;line-height:1.7}
.foot-col h4{font-size:18px;font-weight:600;margin-bottom:6px}
.foot-col ul{list-style:none}
.foot-col li::before{content:"";display:inline-block;width:7px;height:7px;border-radius:50%;background:var(--white);margin-right:10px;vertical-align:middle}
.foot-bottom{position:absolute;left:0;right:0;bottom:0;height:44px;border-top:1px solid rgba(255,255,255,.3);display:flex;justify-content:space-between;align-items:center;padding:0 40px;font-size:13px}
.foot-bottom .links{display:flex;gap:30px}
</style>
</head>
<body>

<header class="section site-header">
  <div class="brand"><span class="brand-dot"></span>The Wellness Barn</div>
  <div class="contact-strip">
    <span><svg width="14" height="14" viewBox="0 0 24 24"><path fill="#2c4420" d="M6.6 10.8a15 15 0 006.6 6.6l2.2-2.2a1 1 0 011-.25 11.4 11.4 0 003.6.57 1 1 0 011 1V20a1 1 0 01-1 1A17 17 0 013 4a1 1 0 011-1h3.5a1 1 0 011 1c0 1.25.2 2.45.57 3.57a1 1 0 01-.25 1z"/></svg>000 555 12</span>
    <span><svg width="14" height="14" viewBox="0 0 24 24"><path fill="#2c4420" d="M3 5h18v14H3z M3 5l9 7 9-7" stroke="#fff" stroke-width="1.5"/></svg>info@thewellnessbarn.com</span>
  </div>
  <nav class="nav">
    <a class="active">Home</a><a>About</a><a>Services</a><a>Testimonials</a><a>Meet Our Team</a><a>FAQ</a>
  </nav>
  <a class="btn">Contact Us</a>
</header>

<section class="section hero" role="img" aria-label="Photo of the training group standing together on the grass outside the clinic">
  <div class="hero-copy">
    <h1>Welcome to The Wellness Barn Willow Bay</h1>
    <p>Rebuild strength and move with confidence. Our physiotherapists and trainers at The Wellness Barn guide you with care and proven programs.</p>
    <a class="btn">Get Started</a>
  </div>
</section>

<section class="section offer">
  <h2>What <span>do we have to offer?</span></h2>
  <p class="intro">The Wellness Barn Willow Bay is dedicated to empowering individuals to achieve their health and wellbeing goals through safe and effective movement. Our core values include integrity, collaboration, inclusivity, and a strong commitment to health. We believe in providing professional support tailored to each individual's needs. Our team, including experienced professionals like Dr. Clara Hollis and Owen Reid, is committed to guiding you on your wellness journey. Join us in fostering a healthier community where everyone can thrive.</p>
  <svg class="arrow" style="left:40px;top:420px" viewBox="0 0 24 24"><path d="M15 4l-8 8 8 8" fill="none" stroke="#1f1f1f" stroke-width="3"/></svg>
  <div class="card-row">
    <div class="offer-card"><div class="photo" role="img" aria-label="Physiotherapy class in the studio"></div><div class="label">Physiotherapy Classes</div></div>
    <div class="offer-card"><div class="photo" role="img" aria-label="Wellness program session" style="background:linear-gradient(140deg,#9a7b55,#4e5d37)"></div><div class="label">Holistic Wellness Programs</div></div>
    <div class="offer-card"><div class="photo" role="img" aria-label="Fresh food for nutrition guidance" style="background:linear-gradient(140deg,#c9a77c,#6f8a45)"></div><div class="label">Personalized Nutrition Guidance</div></div>
  </div>
  <svg class="arrow" style="right:40px;top:420px" viewBox="0 0 24 24"><path d="M9 4l8 8-8 8" fill="none" stroke="#1f1f1f" stroke-width="3"/></svg>
</section>

<section class="section team">
  <p class="eyebrow">Meet Our Team</p>
  <h2>Get to Know Us</h2>
  <p class="sub">Discover the dedicated professionals committed to your health.</p>
  <div class="team-row">
    <div class="member" role="img" aria-label="Portrait of the lead physiotherapist"><span class="share"></span><div class="tag"><b>Dr. Clara Hollis</b>Lead Physiotherapist</div></div>
    <div class="member" role="img" aria-label="Portrait of the wellness coach" style="background:linear-gradient(160deg,#7a6448,#3e4a2e)"><span class="share"></span><div class="tag"><b>Owen Reid</b>Wellness Coach</div></div>
    <div class="member" role="img" aria-label="Portrait of the physiotherapy assistant" style="background:linear-gradient(160deg,#a08e74,#586847)"><span class="share"></span><div class="tag"><b>Mia Tanaka</b>Physiotherapy Assistant</div></div>
  </div>
</section>

<section class="section stories">
  <h2>Client <span>Success Stories</span></h2>
  <p class="sub">Hear from our clients about their transformative journeys with us.</p>
  <svg class="arrow" style="left:40px;top:250px" viewBox="0 0 24 24"><path d="M15 4l-8 8 8 8" fill="none" stroke="#1f1f1f" stroke-width="3"/></svg>
  <div class="story-row">
    <div class="story">
      <div class="who"><div class="avatar" role="img" aria-label="Client portrait"></div><div><div class="name">Laura Bennett</div><div class="role">Fitness Enthusiast</div><div class="stars">★★★★★</div></div></div>
      <p>The Wellness Barn has completely changed my approach to fitness. Their programs are tailored and effective!</p>
    </div>
    <div class="story">
      <div class="who"><div class="avatar" role="img" aria-label="Client portrait"></div><div><div class="name">Peter Walsh</div><div class="role">Retired Veteran</div><div class="stars">★★★★★</div></div></div>
      <p>I never thought I could regain my mobility. The physiotherapy classes here are a game changer!</p>
    </div>
  </div>
  <svg class="arrow" style="right:40px;top:250px" viewBox="0 0 24 24"><path d="M9 4l8 8-8 8" fill="none" stroke="#1f1f1f" stroke-width="3"/></svg>
</section>

<section class="section contact" role="img" aria-label="Dimmed photo of a group workout in the gym">
  <h2>Get in Touch</h2>
  <ul>
    <li><svg width="22" height="22" viewBox="0 0 24 24"><circle cx="12" cy="12" r="12" fill="#fff"/><path d="M6 8h12v8H6z M6 8l6 4 6-4" fill="none" stroke="#2c4420" stroke-width="1.5"/></svg>info@thewellnessbarn.com</li>
    <li><svg width="22" height="22" viewBox="0 0 24 24"><circle cx="12" cy="12" r="12" fill="#fff"/><path fill="#2c4420" d="M9 7h2l1 3-1.5 1a7 7 0 003 3l1-1.5 3 1v2a1 1 0 01-1 1A9 9 0 018 8a1 1 0 011-1z"/></svg>+61 7 4000 1234</li>
    <li><svg width="22" height="22" viewBox="0 0 24 24"><circle cx="12" cy="12" r="12" fill="#fff"/><path fill="#2c4420" d="M12 5a4 4 0 00-4 4c0 3 4 8 4 8s4-5 4-8a4 4 0 00-4-4zm0 5.5A1.5 1.5 0 1112 7.5a1.5 1.5 0 010 3z"/></svg>27 Timber Lane, Willow Bay, Australia, 4600</li>
  </ul>
  <a class="btn btn-light">Contact Us</a>
</section>

<section class="section faq">
  <h2>FAQs</h2>
  <p class="sub">Find answers to common questions about our health and wellness programs, services, and how we can support your journey to better health.</p>
  <div class="faq-photo" role="img" aria-label="Photo of a group class working out in the gym"></div>
  <div class="faq-list">
    <div class="faq-item">
      <div class="faq-q">What types of programs do you offer?<span class="toggle"></span></div>
      <div class="faq-a">We offer a variety of programs including physiotherapy classes, wellness programs, and tailored fitness plans designed for all ages and abilities.</div>
    </div>
    <div class="faq-item"><div class="faq-q">What types of programs do you offer?<span class="toggle"></span></div></div>
    <div class="faq-item"><div class="faq-q">What types of programs do you offer?<span class="toggle"></span></div></div>
  </div>
</section>

<footer class="section site-footer">
  <div class="brand"><span class="brand-dot"></span>The Wellness Barn</div>
  <div class="subscribe"><span>Enter Your Mail</span><b><svg width="20" height="20" viewBox="0 0 24 24"><path fill="#fff" d="M2 21l21-9L2 3v7l15 2-15 2z"/></svg></b></div>
  <div class="socials"><i></i><i></i><i></i><i></i></div>
  <div class="foot-col" style="left:540px">
    <h4>Quick Links</h4>
    <ul><li>Home</li><li>About Us</li><li>Services</li><li>Testimonials</li><li>Meet Our Team</li><li>FAQs</li></ul>
  </div>
  <div class="foot-col" style="left:830px">
    <h4>Contact Us</h4>
    <p>☎ 000 555 12</p>
    <p>✉ info@thewellnessbarn.com</p>
    <p>⌖ 27 Timber Lane, Willow Bay,<br>&nbsp;&nbsp;&nbsp;Australia, 4600</p>
  </div>
  <div class="foot-bottom">
    <div class="links"><span>Terms and Conditions</span><span>Privacy Policy</span></div>
    <span>Copyright ©2025 The Wellness Barn. All Rights Reserved.</span>
  </div>
</footer>

</body>
</html>
```